Business card design for new eCommerce site focusing on integrity and strong businsess tactics

We need a business card that will stand out and be memorable. Something with color that matches our company logo colors. Think high end version of Pactivo. There are 2 logos provided. The parent company is called Amber Ledge Partners and we are presenting a new and very exciting eCommerce site called BrightHarborTrade.example.

Target Market(s)

Our target markets are in the Activities, Food and Beverage, Health and Beauty

Industry/Entity Type

Marketing

Contact Information for Business Card

We have 4 members that need cards...I will provide all info to the winner of the design contest
Business Address is
4870 West 63rd Avenue, Suite C207
Phoenix AZ 85731

Font styles to use
Serif
Sans Serif

Colors

Designer to choose colors to be used in the design.

Requirements
Must have
• The card must be memorable...should be unique in design but must exude integrity and be playful .
• I have provided several colors or our parent company...please feel free to use which ever
Nice to have
• I will leave this up to you. Feel free to use other images of your choosing that wraps around our client.....Activities, Dining, Health, Beauty
Should not have
• just dont be boring

```html
<!DOCTYPE html>
<html lang="en">
<head>
<meta charset="utf-8">
<title>BrightHarborTrade.example Business Card</title>
<link rel="stylesheet" href="https://fonts.googleapis.com/css2?family=Questrial&family=Arimo:wght@400;700&display=swap">
<style>
  :root {
    --backdrop: #e7e4df;
    --brand-green: #7ac143;
    --brand-green-soft: #9bc94a;
    --brand-blue: #2a7ab8;
    --ink: #2b2b2b;
    --paper: #ffffff;
  }
  * { box-sizing: border-box; margin: 0; padding: 0; }
  html, body {
    width: 1200px; height: 900px; overflow: hidden;
    background: var(--backdrop);
  }
  .stage { position: relative; width: 1200px; height: 900px; }
  .card {
    position: absolute; left: 250px; width: 700px; height: 400px;
    box-shadow: 0 4px 14px rgba(0,0,0,0.12);
  }
  .card-front { top: 35px; background: var(--brand-green); }
  .card-back { top: 465px; background: var(--paper); }

  .brand-dot { width: 46px; height: 46px; border-radius: 50%; flex: none; }
  .brand-name {
    font-family: "Questrial", sans-serif; font-size: 30px; line-height: 1;
    white-space: nowrap;
  }

  /* front */
  .front-brand {
    position: absolute; left: 0; right: 0; top: 170px;
    display: flex; align-items: center; justify-content: center; gap: 16px;
  }
  .front-brand .brand-dot { background: var(--paper); }
  .front-brand .brand-name { color: var(--paper); }

  /* back */
  .back-brand {
    position: absolute; left: 40px; top: 50px;
    display: flex; align-items: center; gap: 14px;
  }
  .back-brand .brand-dot { background: var(--brand-green); }
  .back-brand .brand-name { color: var(--brand-green); font-size: 27px; }

  .partner {
    position: absolute; right: 40px; top: 40px; width: 220px;
    text-align: center;
  }
  .partner-mark {
    width: 96px; height: 96px; border-radius: 50%;
    background: var(--brand-green-soft); margin: 0 auto 12px;
  }
  .partner-name {
    font-family: "Arimo", sans-serif; font-weight: 700;
    font-size: 20px; color: var(--brand-green-soft);
  }
  .partner-address {
    margin-top: 26px; text-align: right; font-style: normal;
    font-family: "Arimo", sans-serif; font-size: 14px; line-height: 1.5;
    color: var(--ink);
  }

  .person {
    position: absolute; left: 50px; bottom: 42px;
    font-family: "Arimo", sans-serif;
  }
  .person-name {
    color: var(--brand-blue); font-size: 22px; font-weight: 400;
    letter-spacing: 0.5px; text-transform: uppercase;
  }
  .person-title { color: var(--ink); font-size: 17px; margin-bottom: 14px; }
  .contact-list { list-style: none; }
  .contact-item {
    display: flex; align-items: center; gap: 12px;
    font-size: 17px; color: var(--ink); line-height: 1.5;
  }
  .contact-icon { width: 14px; height: 14px; flex: none; fill: var(--brand-blue); }
  .contact-icon .cut { fill: none; stroke: var(--paper); stroke-width: 1; }
  .contact-icon .line { fill: none; stroke: var(--brand-blue); stroke-width: 1.6; }
</style>
</head>
<body>
<main class="stage">
  <section class="card card-front" aria-label="Card front">
    <div class="front-brand">
      <span class="brand-dot"></span>
      <div class="brand-name">BrightHarborTrade.example</div>
    </div>
  </section>

  <section class="card card-back" aria-label="Card back">
    <div class="back-brand">
      <span class="brand-dot"></span>
      <div class="brand-name">BrightHarborTrade.example</div>
    </div>

    <div class="partner">
      <div class="partner-mark"></div>
      <div class="partner-name">Amber Ledge Partners</div>
      <address class="partner-address">
        4870 West 63rd Avenue,<br>Suite C207 Phoenix AZ 85731
      </address>
    </div>

    <div class="person">
      <div class="person-name">Daniel Reyes</div>
      <div class="person-title">Managing Director</div>
      <ul class="contact-list">
        <li class="contact-item">
          <svg class="contact-icon" viewBox="0 0 16 16" aria-hidden="true"><path d="M3.5 1l2.5 3-1.5 2c1 2 3 4 5 5l2-1.5 3 2.5-1.5 2.5C8 14 2 8 1 2.5z"/></svg>
          (044) 555 0147
        </li>
        <li class="contact-item">
          <svg class="contact-icon" viewBox="0 0 16 16" aria-hidden="true"><path class="line" d="M1 3h14v10H1z M1 3l7 6 7-6"/></svg>
          info@brightharbortrade.example
        </li>
        <li class="contact-item">
          <svg class="contact-icon" viewBox="0 0 16 16" aria-hidden="true"><circle cx="8" cy="8" r="7"/><path class="cut" d="M1 8h14M8 1c3 3 3 11 0 14M8 1c-3 3-3 11 0 14"/></svg>
          www.brightharbortrade.example
        </li>
      </ul>
    </div>
  </section>
</main>
</body>
</html>
```